Wellness bold & beautiful PowerPoint Template

I will like a PowerPoint template, matching my brand, designed for my business.
- Some words that describe our brand identity are: wellness, natural, calming, simplicity, clean
- For icons, we prefer line icons.
- Website: http://www.vendrabo.com/
- PowerPoint board: https://www.pinterest.com/morelistavy/vendrabo-powerpoint/
- Branding board: https://www.pinterest.com/morelistavy/vendrabo-branding/
FYI: I am attaching a rough draft of a powerpoint presentation we are preparing
Target Market(s)
Women 23-48 interested in wellness
Industry/Entity Type
Health And Wellness
Font styles to use
Other font styles liked:
- Open Sans, Helvitica, Meddon
Requirements
Must have
- cover page, about page, author page, table of content, table format, graph format, list format, 2 column template.
Nice to have
- time line page sample

```html
<!DOCTYPE html>
<html lang="en">
<head>
<meta charset="utf-8">
<title>Timeline</title>
<link href="https://fonts.googleapis.com/css2?family=Open+Sans:wght@400;700&display=swap" rel="stylesheet">
<style>
  :root {
    --header-bg: #a6a6a6;
    --header-text: #ffffff;
    --page-bg: #ffffff;
    --event-magenta: #b0278f;
    --event-green: #5f9a3c;
    --body-text: #1a1a1a;
    --rule: #a9a9a9;
    --dot: #a0a0a0;
  }
  html, body {
    margin: 0;
    padding: 0;
    overflow: hidden;
    background: var(--page-bg);
  }
  .slide {
    position: relative;
    width: 1200px;
    height: 675px;
    overflow: hidden;
    background: var(--page-bg);
    font-family: "Open Sans", Helvetica, Arial, sans-serif;
    color: var(--body-text);
  }
  .slide-header {
    position: absolute;
    left: 0; top: 0;
    width: 1200px; height: 68px;
    background: var(--header-bg);
    display: flex;
    align-items: center;
    justify-content: center;
  }
  .slide-title {
    margin: 0;
    color: var(--header-text);
    font-size: 38px;
    font-weight: 700;
    letter-spacing: 1px;
  }
  .timeline-axis {
    position: absolute;
    left: 0; top: 0;
  }
  .event-flag {
    position: absolute;
  }
  .event {
    position: absolute;
    width: 215px;
  }
  .event-title {
    margin: 0;
    font-size: 19px;
    font-weight: 700;
    line-height: 26px;
  }
  .event-dash {
    display: block;
    width: 18px;
    height: 2px;
    background: var(--body-text);
    margin: 10px 0 12px;
  }
  .event-text {
    margin: 0;
    font-size: 14px;
    line-height: 18px;
  }
  .event--right { left: 653px; top: 141px; text-align: left; }
  .event--left { left: 339px; top: 409px; text-align: right; }
  .event--left .event-dash { margin-left: auto; }
  .event--magenta .event-title { color: var(--event-magenta); }
  .event--green .event-title { color: var(--event-green); }
</style>
</head>
<body>
<div class="slide">
  <header class="slide-header">
    <h1 class="slide-title">TIMELINE</h1>
  </header>

  <svg class="timeline-axis" width="1200" height="675" viewBox="0 0 1200 675" aria-hidden="true">
    <line x1="601" y1="209" x2="601" y2="408" stroke="var(--rule)" stroke-width="1.5"/>
    <circle cx="601" cy="209" r="4" fill="var(--dot)"/>
    <circle cx="601" cy="408" r="4" fill="var(--dot)"/>
    <line x1="601" y1="500" x2="601" y2="675" stroke="var(--rule)" stroke-width="1.5"/>
    <circle cx="601" cy="500" r="4" fill="var(--dot)"/>
  </svg>

  <svg class="event-flag" style="left:574px;top:136px" width="58" height="54" viewBox="0 0 58 54" aria-hidden="true">
    <line x1="17" y1="2" x2="3" y2="51" stroke="var(--event-magenta)" stroke-width="4"/>
    <path d="M21 4 C30 6 34 14 38 15 C44 16 50 14 55 18 C50 20 46 24 47 31 C40 26 34 30 28 26 C24 24 18 26 15 25 Z" fill="var(--event-magenta)"/>
  </svg>

  <svg class="event-flag" style="left:574px;top:426px" width="58" height="54" viewBox="0 0 58 54" aria-hidden="true">
    <line x1="17" y1="2" x2="3" y2="51" stroke="var(--event-green)" stroke-width="4"/>
    <path d="M21 4 C30 6 34 14 38 15 C44 16 50 14 55 18 C50 20 46 24 47 31 C40 26 34 30 28 26 C24 24 18 26 15 25 Z" fill="var(--event-green)"/>
  </svg>

  <section class="event event--right event--magenta">
    <h2 class="event-title">EVENT 1</h2>
    <span class="event-dash"></span>
    <p class="event-text">Lorem ipsum dolor sit amet, consectetur adipiscing elit. Aliquam tincidunt ante nec sem congue convallis. Pellentesque vel mauris quis nisl ornare rutrum in id risus.</p>
  </section>

  <section class="event event--left event--green">
    <h2 class="event-title">EVENT 2</h2>
    <span class="event-dash"></span>
    <p class="event-text">Lorem ipsum dolor sit amet, consectetur adipiscing elit. Aliquam tincidunt ante nec sem congue convallis. Pellentesque vel mauris quis nisl ornare rutrum in id risus.</p>
  </section>
</div>
</body>
</html>
```